New Dental Office Needs an Attractive and user friendly Website Designed

I need a website for a new dental office. The Name is Harrowfield Dentistry. I would like a Modern design with a user friendly interface and usability.
I would like a landing page, a page that lists the services we offer: Cosmetic Dentistry, Implants, Dental Hygiene, Emergency Services, Restorations, Dentures
Target Market(s)
Mid to upper class
Industry/Entity Type
Dentistry
Coding
Number of Pages Required
1 page
Requirements
Must have
- Landing page that has a scheduling option, Procedures, operating hours, and contact us info
Nice to have
- Appealing design, Soft comforting colors. Easy to navigate page, Modern and professional.

```html
<!DOCTYPE html>
<html lang="en">
<head>
<meta charset="utf-8">
<title>Harrowfield Dentistry – Landing Page</title>
<link href="https://fonts.googleapis.com/css2?family=Urbanist:wght@400;500;600;700&display=swap" rel="stylesheet">
<style>
:root{
  --navy:#0b2545;
  --blue:#0d8bf2;
  --sky:#1aa3f0;
  --pale:#e7f4fc;
  --card:#ffffff;
  --muted:#8a96a6;
  --grey:#a9b0b8;
  --dark:#0c1a2b;
  --cyan1:#00c8e0;
  --cyan2:#16a9dc;
}
*{box-sizing:border-box;margin:0;padding:0}
html,body{width:1200px;height:1200px;overflow:hidden;background:#fff;font-family:"Urbanist",sans-serif;color:var(--navy)}
.board{position:relative;width:1200px;height:1200px;overflow:hidden;background:#fff}
.abs{position:absolute}
.ph{position:absolute;overflow:hidden}

/* ---------- full page overview column ---------- */
.overview{position:absolute;left:0;top:0;width:215px;height:1200px;overflow:hidden;background:#fff}
.overview .t{position:absolute;white-space:nowrap;line-height:1.15}
.ov-hero-bg{left:0;top:0;width:215px;height:351px;background:var(--pale)}
.ov-logo{left:11px;top:9px;font-size:4.6px;font-weight:700;color:var(--blue)}
.ov-nav{left:76px;top:9px;font-size:2.6px;color:var(--navy);word-spacing:3px}
.ov-book{left:182px;top:7px;width:22px;height:7px;background:var(--blue);border-radius:1.5px}
.ov-h1{left:11px;top:51px;font-size:9.5px;font-weight:600;line-height:1;color:var(--navy)}
.ov-h1 em{font-style:normal;color:var(--sky)}
.ov-btn{left:11px;top:84px;width:21px;height:7px;background:#fff;border-radius:1.5px}
.ov-dot{width:6px;height:6px;border-radius:50%;background:#d98c5f;border:0.6px solid #fff}
.ov-heroimg{left:109px;top:22px;width:95px;height:96px;border-radius:4px;background:linear-gradient(135deg,var(--cyan1),var(--cyan2))}
.ov-c1{left:114px;top:77px;width:42px;height:39px;background:#fff;border-radius:3px}
.ov-c2{left:158px;top:77px;width:42px;height:39px;background:rgba(30,170,230,.75);border-radius:3px}
.ov-sec-h{left:0;width:215px;text-align:center;font-size:8.5px;font-weight:500;top:148px;line-height:1.15;white-space:normal}
.ov-card{top:174px;width:53px;height:60px;background:#fff;border-radius:3px}
.ov-card .i{position:absolute;left:21px;top:14px;width:10px;height:10px;border:0.8px solid var(--sky);border-radius:3px}
.ov-card .n{position:absolute;top:30px;width:100%;text-align:center;font-size:3px}
.ov-card .d{position:absolute;top:36px;left:5px;right:5px;height:1px;background:#d6dde4;box-shadow:0 2.5px 0 #d6dde4}
.ov-vbtn{left:93px;top:244px;width:30px;height:8px;background:var(--blue);border-radius:1.5px}
.ov-mark{top:277px;width:18px;height:5px;background:#c7ced5;border-radius:2px}
.ov-video{left:11px;top:309px;width:194px;height:86px;border-radius:4px;background:linear-gradient(100deg,#6d7d89,#9fb6c4 55%,#3c8fd0)}
.ov-num{font-size:10px;font-weight:500;color:var(--sky)}
.ov-cap{font-size:2.3px;color:var(--navy)}
.band{position:absolute;left:-20px;width:260px;height:22px;white-space:nowrap;font-size:15px;font-weight:500;line-height:22px;padding-left:8px}
.band.grey{top:500px;background:var(--grey);color:#fff;transform:rotate(4deg)}
.band.blue{top:530px;background:var(--blue);color:#fff;transform:rotate(-7deg)}
.ov-news-img{top:629px;width:53px;height:39px;border-radius:2px}
.ov-journey-bg{left:0;top:714px;width:215px;height:267px;background:var(--pale)}
.ov-step{width:8px;height:8px;border-radius:50%;background:var(--sky)}
.ov-tcard{top:889px;width:45px;height:61px;background:#fff;border-radius:2px}
.ov-tcard .s{position:absolute;left:4px;top:5px;font-size:2.6px;color:var(--blue)}
.ov-tcard .b{position:absolute;left:4px;right:4px;top:11px;font-size:2px;line-height:1.2;white-space:normal;color:var(--navy)}
.ov-tcard .a{position:absolute;left:4px;bottom:6px;width:6px;height:6px;border-radius:50%;background:#b48b73}
.ov-tcard .nm{position:absolute;left:12px;bottom:7px;font-size:2px}
.ov-contact-bg{left:0;top:982px;width:215px;height:125px;background:var(--pale)}
.ov-contact-img{left:0;top:985px;width:115px;height:122px;background:linear-gradient(120deg,#d7e9f4,#c79f86 55%,#8bc7ef)}
.ov-form{left:111px;top:993px;width:81px;height:113px;background:#fff;border-radius:3px}
.ov-field{left:117px;width:69px;height:0;border-bottom:0.5px solid #d9dee3}
.ov-send{left:117px;top:1080px;width:69px;height:7px;background:var(--blue);border-radius:1px}
.ov-footer{left:0;top:1107px;width:215px;height:93px;background:var(--dark)}
.ov-foot-t{font-size:2.2px;color:#9aa6b4;line-height:1.6}
.ov-bigname{left:9px;top:1150px;font-size:35px;font-weight:700;color:var(--blue);letter-spacing:-1px}

/* ---------- zoomed detail ---------- */
.detail{position:absolute;left:474px;top:0;width:726px;height:1200px;overflow:hidden;background:#fff}
.detail-bg{position:absolute;left:0;top:0;width:726px;height:1169px;background:var(--pale)}
.brand{position:absolute;left:40px;top:12px;font-size:15px;font-weight:700;color:var(--blue);display:flex;align-items:center;gap:5px;white-space:nowrap}
.brand .dot{width:7px;height:7px;border-radius:50%;background:var(--blue)}
.nav{position:absolute;top:15px;left:0;width:100%}
.nav a{position:absolute;font-size:8.5px;font-weight:600;color:var(--navy);text-decoration:none;white-space:nowrap}
.nav a.on{color:var(--muted);font-weight:500}
.phone{position:absolute;left:534px;top:15px;font-size:8.5px;font-weight:600;display:flex;align-items:center;gap:6px;white-space:nowrap}
.btn-book{position:absolute;left:614px;top:8px;width:75px;height:25px;background:var(--blue);color:#fff;border-radius:4px;font-size:8px;font-weight:500;display:flex;align-items:center;justify-content:center;gap:4px}
.eyebrow{position:absolute;font-size:7px;font-weight:600;letter-spacing:.9px;color:var(--navy);white-space:nowrap}
.hero-title{position:absolute;left:36px;top:156px;font-size:35px;font-weight:600;line-height:31px;letter-spacing:-1.2px;white-space:nowrap}
.hero-title .accent{color:var(--sky)}
.tooth{display:inline-block;width:19px;height:19px;border-radius:50%;background:var(--sky);vertical-align:1px;margin:0 4px 0 3px;position:relative}
.tooth svg{position:absolute;left:4px;top:3px}
.btn-white{position:absolute;left:36px;top:266px;width:72px;height:28px;background:#fff;border-radius:4px;font-size:8.5px;font-weight:600;display:flex;align-items:center;justify-content:center}
.avatars{position:absolute;left:36px;top:354px;display:flex}
.avatars span{width:29px;height:29px;border-radius:50%;border:2px solid #fff;margin-right:-6px}
.rating{position:absolute;left:122px;top:357px;font-size:8.5px;line-height:14px;color:var(--navy)}
.rating .stars{color:var(--blue);letter-spacing:.5px}
.hero-photo{position:absolute;left:370px;top:59px;width:319px;height:325px;border-radius:15px;background:radial-gradient(circle at 55% 40%,#55dbeb 0,var(--cyan1) 40%,var(--cyan2) 100%)}
.hero-card{position:absolute;top:240px;width:140px;height:129px;border-radius:10px}
.hero-card.light{left:386px;background:#f6f8fa;color:var(--navy)}
.hero-card.tint{left:535px;background:rgba(24,176,226,.72);color:#fff}
.hero-card .ring{position:absolute;left:15px;top:16px;width:25px;height:25px;border-radius:50%;border:1px solid rgba(140,160,180,.35);display:flex;align-items:center;justify-content:center}
.hero-card.tint .ring{border-color:rgba(255,255,255,.7)}
.hero-card p{position:absolute;left:15px;top:60px;font-size:14.5px;font-weight:500;line-height:17.5px;white-space:nowrap}
.section-title{position:absolute;left:0;width:726px;text-align:center;font-size:30px;font-weight:500;line-height:33px;letter-spacing:-.5px;top:481px}
.svc{position:absolute;top:573px;width:178px;height:203px;background:var(--card);border-radius:14px;text-align:center}
.svc svg{position:absolute;left:72px;top:52px}
.svc h3{position:absolute;top:101px;width:100%;font-size:12px;font-weight:600}
.svc p{position:absolute;top:123px;left:14px;right:14px;font-size:8.5px;line-height:13.5px;color:var(--muted)}
.btn-blue{position:absolute;left:313px;top:807px;width:100px;height:29px;background:var(--blue);color:#fff;border-radius:4px;font-size:8.5px;font-weight:500;display:flex;align-items:center;justify-content:center}
.partner{position:absolute;top:920px;height:20px;background:#cdd3d9;border-radius:10px}
.video{position:absolute;left:36px;top:1025px;width:653px;height:200px;border-radius:16px;background:linear-gradient(100deg,#8a9aa4 0,#b9c6cc 40%,#c8a08a 70%,#3f9be0 100%)}
.play{position:absolute;left:338px;top:1145px;width:50px;height:50px;border-radius:50%;border:1.4px solid rgba(255,255,255,.9);display:flex;align-items:center;justify-content:center}
</style>
</head>
<body>
<div class="board">

  <!-- full page overview -->
  <div class="overview">
    <div class="abs ov-hero-bg"></div>
    <div class="t ov-logo">Harrowfield Dentistry</div>
    <div class="t ov-nav">Home About Services FAQ Blog Contact</div>
    <div class="t" style="left:158px;top:9px;font-size:2.6px">555-210-8834</div>
    <div class="abs ov-book"></div>
    <div class="t" style="left:11px;top:45px;font-size:2.2px;letter-spacing:.2px">OUR HARROWFIELD SERVICES</div>
    <div class="t ov-h1">Personalized<br>dental <span style="color:var(--sky)">●</span> solutions<br>for <em>every patient</em></div>
    <div class="abs ov-btn"></div>
    <div class="abs" style="left:11px;top:110px;display:flex">
      <span class="ov-dot"></span><span class="ov-dot" style="background:#c9a37f;margin-left:-1px"></span><span class="ov-dot" style="background:#e0622f;margin-left:-1px"></span>
    </div>
    <div class="t" style="left:36px;top:110px;font-size:2.4px;color:var(--navy)">5/5 <span style="color:var(--blue)">★★★★★</span><br>38 Reviews On Smilelist</div>
    <div class="ph ov-heroimg" role="img" aria-label="Smiling young patient on a turquoise backdrop"></div>
    <div class="abs ov-c1"></div>
    <div class="abs ov-c2"></div>
    <div class="t" style="left:119px;top:95px;font-size:3.3px;line-height:1.3">Complete Family<br>Dentist for Every<br>Smile</div>
    <div class="t" style="left:163px;top:95px;font-size:3.3px;line-height:1.3;color:#fff">Comprehensive<br>dental care in<br>our clinic</div>

    <div class="t" style="left:0;width:215px;text-align:center;top:142px;font-size:2px">OUR SERVICES</div>
    <div class="t ov-sec-h">Complete family dentist<br>for every smile</div>
    <div class="abs ov-card" style="left:24px"><span class="i"></span><span class="n">Cosmetic Dentistry</span><span class="d"></span></div>
    <div class="abs ov-card" style="left:81px"><span class="i"></span><span class="n">Implants</span><span class="d"></span></div>
    <div class="abs ov-card" style="left:138px"><span class="i"></span><span class="n">Dental Hygiene</span><span class="d"></span></div>
    <div class="abs ov-vbtn"></div>
    <div class="abs ov-mark" style="left:25px"></div>
    <div class="abs ov-mark" style="left:58px;width:9px"></div>
    <div class="abs ov-mark" style="left:88px;width:11px"></div>
    <div class="abs ov-mark" style="left:112px;width:20px"></div>
    <div class="abs ov-mark" style="left:143px;width:14px"></div>
    <div class="abs ov-mark" style="left:172px;width:14px"></div>

    <div class="ph ov-video" role="img" aria-label="Patient smiling in a dental chair, with play button"></div>

    <div class="t" style="left:11px;top:417px;font-size:4.3px;font-weight:600">The numbers speak for us</div>
    <div class="t" style="left:11px;top:427px;font-size:2px;color:var(--muted);line-height:1.5">Harrowfield Dentistry has cared for over 1,200 happy<br>patients, 2,000 cleanings, 99% satisfaction.</div>
    <div class="t ov-num" style="left:109px;top:415px">60%</div><div class="t ov-cap" style="left:109px;top:430px">Repeat clients</div>
    <div class="t ov-num" style="left:159px;top:415px">35+</div><div class="t ov-cap" style="left:159px;top:430px">Clients served</div>
    <div class="t ov-num" style="left:11px;top:452px">8</div><div class="t ov-cap" style="left:11px;top:467px">Experience</div>
    <div class="t ov-num" style="left:60px;top:452px">250+</div><div class="t ov-cap" style="left:60px;top:467px">Happy Patients</div>
    <div class="t ov-num" style="left:109px;top:452px">857</div><div class="t ov-cap" style="left:109px;top:467px">Dental implants</div>
    <div class="t ov-num" style="left:159px;top:452px">999+</div><div class="t ov-cap" style="left:159px;top:467px">Bright Smiles</div>

    <div class="band grey">Care for Your Best Smile / Trusted Care for Your Best Smile</div>
    <div class="band blue">mile / Trusted Care for Your Best Smile / Trusted</div>

    <div class="t" style="left:23px;top:594px;font-size:2px">DENTAL PRACTICE</div>
    <div class="t" style="left:110px;top:593px;font-size:8px;line-height:1.15;color:var(--muted)"><span style="color:var(--sky)">Latest news and<br>insights</span> from the<br>industry</div>
    <div class="ph ov-news-img" style="left:24px;background:linear-gradient(135deg,#7ec6e8,#cfe8f4)" role="img" aria-label="Electric toothbrush on a blue background"></div>
    <div class="ph ov-news-img" style="left:81px;background:linear-gradient(135deg,#f3d9b8,#e3b78c)" role="img" aria-label="Smiling woman with bright teeth"></div>
    <div class="ph ov-news-img" style="left:138px;background:linear-gradient(135deg,#e8eef2,#9aa8b1)" role="img" aria-label="Modern dental treatment room"></div>
    <div class="t" style="left:24px;top:671px;font-size:2px;color:var(--muted)">HEALTH</div>
    <div class="t" style="left:24px;top:675px;font-size:3.3px;line-height:1.25">How to maintain a healthy<br>smile every day</div>
    <div class="t" style="left:81px;top:671px;font-size:2px;color:var(--muted)">HEALTH</div>
    <div class="t" style="left:81px;top:675px;font-size:3.3px;line-height:1.25">The importance of regular<br>dental checkups</div>
    <div class="t" style="left:138px;top:671px;font-size:2px;color:var(--muted)">TREATMENT</div>
    <div class="t" style="left:138px;top:675px;font-size:3.3px;line-height:1.25">Choosing the right dental<br>treatment for you</div>

    <div class="abs ov-journey-bg"></div>
    <div class="t" style="left:23px;top:738px;font-size:2px">STEP BY STEP</div>
    <div class="t" style="left:23px;top:745px;font-size:8px;line-height:1.15">Our patients'<br>journey to healthy</div>
    <div class="abs ov-step" style="left:23px;top:771px"></div>
    <div class="t" style="left:36px;top:773px;font-size:3px">Research &amp; Strategy</div>
    <div class="t" style="left:36px;top:779px;font-size:2px;color:var(--muted);line-height:1.4">We help tailor your dental care plan<br>through honest strategies.</div>
    <div class="abs ov-step" style="left:23px;top:793px"></div>
    <div class="t" style="left:36px;top:795px;font-size:3px">Dental Care</div>
    <div class="t" style="left:36px;top:801px;font-size:2px;color:var(--muted);line-height:1.4">Gentle care that keeps you relaxed<br>with modern, proven technology.</div>
    <div class="abs ov-step" style="left:23px;top:815px"></div>
    <div class="t" style="left:36px;top:817px;font-size:3px">Patient Comfort</div>
    <div class="t" style="left:36px;top:823px;font-size:2px;color:var(--muted);line-height:1.4">We prioritize patient comfort with tailored<br>care and calming spaces.</div>
    <div class="ph" style="left:110px;top:737px;width:82px;height:96px;border-radius:3px;background:linear-gradient(135deg,#e9eef1,#b7a08f 60%,#d9e4ea)" role="img" aria-label="Dentist showing a jaw model to a patient"></div>

    <div class="t" style="left:0;width:215px;text-align:center;top:855px;font-size:2px">TESTIMONIALS</div>
    <div class="t" style="left:0;width:215px;text-align:center;top:861px;font-size:8px;line-height:1.2"><span style="color:var(--sky)">Smiles Speak</span><br>Louder Than Words</div>
    <div class="abs ov-tcard" style="left:11px"><span class="s">★★★★★</span><span class="b">Harrowfield Dentistry transformed my dental experience with their compassionate care and modern technology. I felt at ease throughout my treatment.</span><span class="a"></span><span class="nm">Nora Pell</span></div>
    <div class="abs ov-tcard" style="left:61px"><span class="s">★★★★★</span><span class="b">The team at Harrowfield is exceptional. They took the time to explain every step and made me feel comfortable. My smile has never looked better!</span><span class="a"></span><span class="nm">Elias Brandt</span></div>
    <div class="abs ov-tcard" style="left:110px;height:57px"><span class="s">★★★★★</span><span class="b">Harrowfield Dentistry transformed my dental experience! The staff is friendly and the care is top notch. I felt at ease during treatment.</span><span class="a"></span><span class="nm">Ivy Castell</span></div>
    <div class="abs ov-tcard" style="left:159px;height:57px"><span class="s">★★★★★</span><span class="b">Every visit to Harrowfield has been wonderful. The team is professional and I always leave with a brighter smile. Truly unmatched!</span><span class="a"></span><span class="nm">Theo Marsh</span></div>

    <div class="abs ov-contact-bg"></div>
    <div class="ph ov-contact-img" role="img" aria-label="Laughing man during a dental check-up"></div>
    <div class="abs ov-form"></div>
    <div class="t" style="left:117px;top:1000px;font-size:4.5px;line-height:1.2">Have questions?<br>Get in touch!</div>
    <div class="abs ov-field" style="top:1019px"></div>
    <div class="abs ov-field" style="top:1030px"></div>
    <div class="abs ov-field" style="top:1041px"></div>
    <div class="abs" style="left:117px;top:1046px;width:69px;height:22px;border:0.5px solid #d9dee3"></div>
    <div class="t" style="left:117px;top:1073px;font-size:1.8px;color:var(--muted)">I agree that my submitted data is being collected and stored.</div>
    <div class="abs ov-send"></div>

    <div class="abs ov-footer"></div>
    <div class="t ov-foot-t" style="left:11px;top:1120px">12 Maple Row, Suite 4<br>Harrowfield, 00000<br>Mon–Fri 8am–6pm<br>Sat 9am–2pm</div>
    <div class="t ov-foot-t" style="left:50px;top:1120px">hello@harrowfield.example<br>+1 555 210 8834</div>
    <div class="t ov-foot-t" style="left:89px;top:1120px">Updates<br>Community<br>Gallery<br>Videos</div>
    <div class="t ov-foot-t" style="left:147px;top:1120px">© Harrowfield Dentistry 2025. All Rights Reserved.</div>
    <div class="t ov-bigname">Harrowfield</div>
  </div>

  <!-- zoomed detail -->
  <div class="detail">
    <div class="detail-bg"></div>

    <header>
      <div class="brand"><span class="dot"></span>Harrowfield Dentistry</div>
      <nav class="nav">
        <a class="on" style="left:256px">Home</a>
        <a style="left:294px">About</a>
        <a style="left:331px">Services</a>
        <a style="left:378px">FAQ</a>
        <a style="left:409px">Blog</a>
        <a style="left:440px">Contact</a>
      </nav>
      <div class="phone">
        <svg width="11" height="11" viewBox="0 0 24 24" fill="none" stroke="#0b2545" stroke-width="1.6"><path d="M5 3h4l2 5-2.5 1.5a11 11 0 0 0 6 6L16 13l5 2v4a2 2 0 0 1-2 2A17 17 0 0 1 3 5a2 2 0 0 1 2-2z"/></svg>
        555-210-8834
      </div>
      <div class="btn-book">Book Now
        <svg width="8" height="8" viewBox="0 0 24 24" fill="none" stroke="#fff" stroke-width="2"><rect x="3" y="5" width="18" height="16" rx="2"/><path d="M8 3v4M16 3v4M8 13l3 3 5-5"/></svg>
      </div>
    </header>

    <section class="hero">
      <div class="eyebrow" style="left:36px;top:138px">OUR HARROWFIELD SERVICES</div>
      <h1 class="hero-title">Personalized<br>dental<span class="tooth"><svg width="11" height="13" viewBox="0 0 24 28" fill="#fff"><path d="M12 3C8 0 2 1 2 8c0 5 2 7 3 12 .6 3 1.5 6 3 6s2-6 4-6 2.5 6 4 6 2.4-3 3-6c1-5 3-7 3-12 0-7-6-8-10-5z"/></svg></span>solutions<br>for <span class="accent">every patient</span></h1>
      <div class="btn-white">Book Now</div>
      <div class="avatars">
        <span style="background:#d9a27f"></span><span style="background:#c9ab88"></span><span style="background:#e2612c"></span>
      </div>
      <div class="rating">5/5 <span class="stars">★★★★★</span><br>38 Review On Smilelist</div>

      <div class="hero-photo" role="img" aria-label="Smiling young woman pointing at her smile on a turquoise backdrop"></div>
      <div class="hero-card light">
        <span class="ring"><svg width="9" height="9" viewBox="0 0 24 24" fill="none" stroke="#0b2545" stroke-width="2"><path d="M4 12h15M13 6l6 6-6 6"/></svg></span>
        <p>Complete Family<br>Dentistfor Every<br>Smile</p>
      </div>
      <div class="hero-card tint">
        <span class="ring"><svg width="9" height="9" viewBox="0 0 24 24" fill="none" stroke="#fff" stroke-width="2"><path d="M4 12h15M13 6l6 6-6 6"/></svg></span>
        <p>Comprehensive<br>dental care in<br>our clinic</p>
      </div>
    </section>

    <section class="services">
      <div class="eyebrow" style="left:0;width:726px;text-align:center;top:461px">OUR SERVICES</div>
      <h2 class="section-title">Complete family dentist<br>for every smile</h2>

      <article class="svc" style="left:80px">
        <svg width="34" height="34" viewBox="0 0 34 34" fill="none" stroke="#1aa3f0" stroke-width="1.3"><rect x="7" y="2" width="20" height="30" rx="3"/><path d="M11 9c0-3 3-4 6-2 3-2 6-1 6 2 0 2-1 3-2 4H13c-1-1-2-2-2-4z"/><path d="M13 15h8M14 19h6M15 23h4M16 27h2"/></svg>
        <h3>Cosmetic Dentistry</h3>
        <p>We offer teeth whitening, veneers, and bonding to enhance your smile.</p>
      </article>
      <article class="svc" style="left:274px">
        <svg width="34" height="34" viewBox="0 0 34 34" fill="none" stroke="#1aa3f0" stroke-width="1.3"><path d="M9 8c0-4 4-5 8-3 4-2 8-1 8 3 0 3-2 4-3 6H12c-1-2-3-3-3-6z"/><path d="M12 17h10M13 21h8M14 25h6M15 29h4"/></svg>
        <h3>Implants</h3>
        <p>We replace missing teeth with durable implants that look and feel natural.</p>
      </article>
      <article class="svc" style="left:468px">
        <svg width="34" height="34" viewBox="0 0 34 34" fill="none" stroke="#1aa3f0" stroke-width="1.3"><circle cx="15" cy="17" r="11"/><path d="M10 14c0-3 3-4 5-2 2-2 5-1 5 2 0 3-1 4-1.5 7-.3 2-1.3 2-1.7 0-.3-1.5-1-2-1.8-2s-1.5.5-1.8 2c-.4 2-1.4 2-1.7 0C11 18 10 17 10 14z"/><rect x="22" y="3" width="10" height="7" rx="2"/><path d="M24 6h6M23 26l6 6"/></svg>
        <h3>Dental Hygiene</h3>
        <p>We offer gentle cleanings and checkups to keep your gums healthy.</p>
      </article>

      <div class="btn-blue">View All Services</div>
    </section>

    <section class="partners" aria-label="Partner brands">
      <div class="partner" style="left:83px;width:72px"></div>
      <div class="partner" style="left:202px;width:30px;height:30px;top:915px;border-radius:50%"></div>
      <div class="partner" style="left:297px;width:36px"></div>
      <div class="partner" style="left:377px;width:70px"></div>
      <div class="partner" style="left:485px;width:46px"></div>
      <div class="partner" style="left:584px;width:44px"></div>
    </section>

    <section class="intro-video">
      <div class="video" role="img" aria-label="Smiling woman seated in a dental chair in a bright clinic"></div>
      <div class="play"><svg width="9" height="10" viewBox="0 0 9 10"><path d="M1 0l8 5-8 5z" fill="#fff"/></svg></div>
    </section>
  </div>

</div>
</body>
</html>
```